Business Card Design for Occupational Medicine Start Up Company

We need to design a professional business card. We are a healthcare company providing occupational medicine services to blue collar industries. We are professional, efficient and high quality service providers.

Target Market(s)

Blue Collar Industry: Shipbuilding, Ports, Trucking Companies; The Executives and Safety Officers for these companies

Industry/Entity Type

Healthcare

Contact Information for Business Card

Logo, Name, Title, Email, Phone

Other font styles liked:
• Please match our Brand Guide

Requirements
Must have
• Our Company Colors and Logo

```html
<!DOCTYPE html>
<html lang="en">
<head>
<meta charset="utf-8">
<title>CrewWell Clinics – Business Card</title>
<link rel="stylesheet" href="https://fonts.googleapis.com/css2?family=Montserrat:wght@600;700&family=Roboto:wght@400;500;700&display=swap">
<style>
  :root {
    --backdrop: #1b1b1b;
    --brand-blue: #1f9fdd;
    --brand-blue-deep: #1684d0;
    --brand-navy: #26307a;
    --text-grey: #3c3f48;
    --paper: #ffffff;
  }
  * { box-sizing: border-box; margin: 0; padding: 0; }
  html, body { width: 1200px; height: 800px; overflow: hidden; }
  body {
    background: var(--backdrop);
    font-family: "Roboto", Arial, sans-serif;
    position: relative;
  }
  .card {
    position: absolute;
    top: 252px;
    width: 520px;
    height: 297px;
    overflow: hidden;
  }
  /* Back side */
  .card-back {
    left: 50px;
    background: linear-gradient(120deg, var(--brand-blue-deep) 0%, var(--brand-blue) 60%, #22a6e0 100%);
    color: var(--paper);
  }
  .back-brand {
    position: absolute;
    top: 104px; left: 0; right: 0;
    text-align: center;
    font-family: "Montserrat", Arial, sans-serif;
    font-weight: 700;
    font-size: 30px;
    letter-spacing: 2px;
    color: var(--paper);
  }
  .back-url {
    position: absolute;
    bottom: 38px; left: 0; right: 0;
    text-align: center;
    font-size: 11px;
    letter-spacing: 3.5px;
    color: var(--paper);
  }
  .back-url strong { font-weight: 700; }
  /* Front side */
  .card-front {
    left: 630px;
    background: var(--paper);
  }
  .front-brand {
    position: absolute;
    top: 58px; right: 34px;
    display: flex; align-items: center; gap: 8px;
    font-family: "Montserrat", Arial, sans-serif;
    font-weight: 700;
    font-size: 21px;
    line-height: 28px;
    color: var(--brand-navy);
    letter-spacing: .5px;
  }
  .brand-dot {
    width: 14px; height: 14px; border-radius: 50%;
    background: var(--brand-navy);
  }
  .person {
    position: absolute;
    top: 108px; left: 36px;
  }
  .person-name {
    font-size: 20px; line-height: 24px; font-weight: 700; color: var(--brand-navy);
  }
  .person-title {
    font-size: 13px; line-height: 16px; color: var(--brand-blue); margin-top: 2px;
  }
  .divider {
    position: absolute;
    top: 160px; left: 36px; right: 34px;
    height: 1px; background: var(--brand-navy);
  }
  .contact-list {
    position: absolute;
    top: 194px; left: 36px;
    list-style: none;
    font-size: 11.5px; color: var(--text-grey);
    line-height: 16px;
  }
  .contact-list li { display: flex; align-items: center; gap: 8px; }
  .contact-list svg { width: 10px; height: 10px; fill: var(--brand-blue); }
  .address {
    position: absolute;
    top: 172px; right: 34px;
    text-align: right;
    font-style: normal;
    font-size: 11.5px; color: var(--text-grey);
    line-height: 16px;
  }
  .address .url { color: var(--brand-blue); }
  .band-navy {
    position: absolute; left: 0; bottom: 0;
    width: 300px; height: 12px; background: var(--brand-navy);
  }
  .band-blue {
    position: absolute; right: 0; bottom: 0;
    width: 216px; height: 12px; background: var(--brand-blue);
  }
</style>
</head>
<body>
  <section class="card card-back" aria-label="Card back">
    <div class="back-brand">CrewWell Clinics</div>
    <div class="back-url">www.<strong>CrewWellClinics</strong>.com</div>
  </section>

  <section class="card card-front" aria-label="Card front">
    <div class="front-brand"><span class="brand-dot"></span>CREWWELL CLINICS</div>

    <div class="person">
      <div class="person-name">Daniel Reyes</div>
      <div class="person-title">President</div>
    </div>

    <div class="divider"></div>

    <ul class="contact-list">
      <li><svg viewBox="0 0 10 10" aria-hidden="true"><path d="M2 0.5 L3.6 2.6 L2.7 3.6 Q3.8 5.9 6.4 7.3 L7.4 6.4 L9.5 8 L8.4 9.5 Q1 8 0.5 1.6 Z"/></svg>555-214-7730</li>
      <li><svg viewBox="0 0 10 10" aria-hidden="true"><path d="M2.5 0 H7.5 V10 H2.5 Z M3.3 1 V8 H6.7 V1 Z"/></svg>555-318-6042</li>
      <li><svg viewBox="0 0 10 10" aria-hidden="true"><path d="M2.5 0 H7.5 V3 H10 V8 H0 V3 H2.5 Z M1.5 8.5 H8.5 V10 H1.5 Z"/></svg>555-407-2915</li>
      <li><svg viewBox="0 0 10 10" aria-hidden="true"><path d="M0 2 H10 V8.5 H0 Z M0.8 2.6 L5 5.6 L9.2 2.6 Z"/></svg>hello@crewwellclinics.com</li>
    </ul>

    <address class="address">
      Harbor Point Medical Offices<br>
      412 Dockside Avenue<br>
      Portview, Maine 04021<br>
      <span class="url">www.crewwellclinics.com</span>
    </address>

    <div class="band-navy"></div>
    <div class="band-blue"></div>
  </section>
</body>
</html>
```